Red Mo's Wine Label Project

We need a new entry level wine label called "Red Mo's" for a range of wines we are developing from inland Australia. Our company is made up of three youngish guys who live hard and love taking the mickey. Red Mo is Red Morrie - the largest and loudest of the three partners (and ideally this label will take the mickey out of him). We've grown the grapes ourselves for this first release which will be a 2012 Pinot Gris. Wine style is dry, young, fresh and contemporary and pitched at the sub AUD $10 retail price point. The package will be flint (clear) claret shape bottle with plain screwcap (colour matched to suit the winning label design).

I've attached a couple of photos of Red Morrie to give you some idea of his presence and persona.

Target Market(s)

Semi educated 25 - 40 year old wine drinkers. Skewed towards females.

Industry/Entity Type

Retail

Requirements
Should not have
• Anything traditional or old fashioned

```html
<!DOCTYPE html>
<html lang="en">
<head>
<meta charset="utf-8">
<title>Red Mo's – Pinot Gris Labels</title>
<link rel="stylesheet" href="https://fonts.googleapis.com/css2?family=Bebas+Neue&family=Raleway:wght@400&display=swap">
<style>
  :root {
    --backdrop: #f3f3f3;
    --ink: #1e1e1e;
    --silver-edge: #c9c9c9;
    --silver-mid: #ececec;
    --paper: #ffffff;
    --band-green: #3d7b47;
    --band-green-light: #5f9a66;
    --band-crimson: #b3265a;
    --band-crimson-light: #cf3f73;
    --band-text: rgba(255, 255, 255, 0.9);
    --engraving-dark: #3a3a3a;
    --engraving-light: #a8a8a8;
  }

  * { box-sizing: border-box; margin: 0; padding: 0; }

  html, body {
    width: 1037px;
    height: 1200px;
    overflow: hidden;
  }

  body {
    background: var(--backdrop);
    display: flex;
    align-items: center;
    justify-content: center;
    gap: 44px;
  }

  .label {
    position: relative;
    width: 460px;
    height: 440px;
    display: flex;
    flex-direction: column;
    box-shadow: 0 2px 10px rgba(0, 0, 0, 0.12);
  }

  .label--white-wine {
    background: linear-gradient(90deg,
      var(--silver-edge) 0%,
      var(--silver-mid) 22%,
      var(--paper) 50%,
      var(--silver-mid) 78%,
      var(--silver-edge) 100%);
  }

  .label--red-wine {
    background: linear-gradient(90deg,
      #e4e4e4 0%,
      var(--paper) 18%,
      var(--paper) 82%,
      #e4e4e4 100%);
  }

  .label__mark {
    flex: 1;
    display: flex;
    align-items: center;
    justify-content: center;
    gap: 6px;
    padding-top: 10px;
  }

  .label__name {
    font-family: "Bebas Neue", "Oswald", sans-serif;
    font-size: 118px;
    line-height: 1;
    color: var(--ink);
    letter-spacing: 1px;
    padding-top: 30px;
  }

  .label__artwork {
    width: 120px;
    height: 180px;
    background: linear-gradient(180deg, var(--engraving-dark), var(--engraving-light));
    opacity: 0.85;
  }

  .label__artwork--press {
    width: 130px;
    height: 170px;
    margin-top: 40px;
  }

  .label__artwork--corkscrew {
    width: 110px;
    height: 190px;
  }

  .label__band {
    height: 74px;
    display: flex;
    align-items: center;
    justify-content: center;
    font-family: "Raleway", "Helvetica Neue", sans-serif;
    font-size: 21px;
    letter-spacing: 1.5px;
    text-transform: uppercase;
    color: var(--band-text);
    white-space: nowrap;
  }

  .label--white-wine .label__band {
    background: linear-gradient(90deg, var(--band-green), var(--band-green-light) 50%, var(--band-green));
  }

  .label--red-wine .label__band {
    background: linear-gradient(90deg, var(--band-crimson), var(--band-crimson-light) 50%, var(--band-crimson));
    margin-bottom: 0;
  }

  .label__sep { margin: 0 12px; }
</style>
</head>
<body>

  <section class="label label--white-wine">
    <div class="label__mark">
      <span class="label__name">Red Mo</span>
      <div class="label__artwork label__artwork--press" role="img" aria-label="Engraved illustration of a wooden barrel wine press"></div>
    </div>
    <div class="label__band">
      Pinot Gris<span class="label__sep">|</span>2012<span class="label__sep">|</span>Alkohol 12%
    </div>
  </section>

  <section class="label label--red-wine">
    <div class="label__mark">
      <span class="label__name">Red Mo</span>
      <div class="label__artwork label__artwork--corkscrew" role="img" aria-label="Engraved illustration of a T-handle corkscrew"></div>
    </div>
    <div class="label__band">
      Pinot Gris<span class="label__sep">|</span>2012<span class="label__sep">|</span>Alkohol 12%
    </div>
  </section>

</body>
</html>
```